Velmor Spire Nine Flash website

we need a website to cater to 2 aspect of the business. We have Velmor spire residence and velmor spire office. For the office, we will get their inquire and arrange a face to face meetup to show them the office area for rent. For the residence side, it will need to be like staylane or roomvio.com. we want to allow them to book online for the date they need. We have a total of 10 different room configurations starting at $70 per night and up depending on the size of the room. example of the design is https://brisquelodge.com/

Target Market(s)

the website should have detail information on the layout, designs, and luxury of the building.

Industry/Entity Type

office and service appartment rental/lease

Coding

Coded - Design and coding required

Number of Pages Required

5+ page

Requirements
Must have
• a luxury perspective
Nice to have
• example https://brisquelodge.com/

```html
<!DOCTYPE html>
<html lang="en">
<head>
<meta charset="UTF-8">
<title>Velmor Spire Nine — Choose Your Space</title>
<link rel="stylesheet" href="https://fonts.googleapis.com/css2?family=Cinzel:wght@400&family=Playfair+Display:wght@700&family=Poppins:wght@600&display=swap">
<style>
  :root {
    --gold: #d59a2a;
    --white: #ffffff;
    --office-light: #efe0b4;
    --office-mid: #d6b56d;
    --office-deep: #9c7d45;
    --office-shadow: #6f5a33;
    --residence-light: #5a5d63;
    --residence-mid: #33363b;
    --residence-deep: #17181b;
  }
  * { box-sizing: border-box; margin: 0; padding: 0; }
  html, body {
    width: 1200px;
    height: 557px;
    overflow: hidden;
    background: var(--residence-deep);
  }
  .split-landing {
    position: relative;
    width: 1200px;
    height: 557px;
    overflow: hidden;
  }
  .backdrop {
    position: absolute;
    inset: 0;
    width: 1200px;
    height: 557px;
  }
  .brand-panel {
    position: absolute;
    top: 108px;
    width: 440px;
    display: flex;
    flex-direction: column;
    align-items: center;
    text-align: center;
  }
  .brand-panel--office { left: 71px; }
  .brand-panel--residence { left: 697px; }
  .brand-mark {
    width: 118px;
    height: 118px;
    border: 2px solid currentColor;
    margin-bottom: 44px;
  }
  .brand-panel--office .brand-mark { color: var(--white); }
  .brand-panel--residence .brand-mark { color: var(--gold); }
  .brand-name {
    font-family: "Cinzel", serif;
    font-weight: 400;
    font-size: 37px;
    line-height: 1;
    letter-spacing: 0.5px;
    white-space: nowrap;
  }
  .brand-panel--office .brand-name { color: var(--white); }
  .brand-panel--residence .brand-name { color: var(--gold); }
  .space-title {
    font-family: "Playfair Display", serif;
    font-weight: 700;
    font-size: 46px;
    line-height: 1;
    letter-spacing: 1px;
    color: var(--white);
    margin-top: 18px;
  }
  .enter-button {
    display: flex;
    align-items: center;
    justify-content: center;
    width: 168px;
    height: 46px;
    border-radius: 23px;
    margin-top: 24px;
    font-family: "Poppins", sans-serif;
    font-weight: 600;
    font-size: 14px;
    color: var(--white);
    text-decoration: none;
    letter-spacing: 0.3px;
  }
  .enter-button--outline { border: 2px solid var(--white); background: transparent; }
  .enter-button--solid { background: var(--gold); }
</style>
</head>
<body>
<main class="split-landing">
  <svg class="backdrop" viewBox="0 0 1200 557" xmlns="http://www.w3.org/2000/svg">
    <defs>
      <linearGradient id="office-tone" x1="0" y1="0" x2="0.8" y2="1">
        <stop offset="0" stop-color="var(--office-light)"/>
        <stop offset="0.45" stop-color="var(--office-mid)"/>
        <stop offset="0.8" stop-color="var(--office-deep)"/>
        <stop offset="1" stop-color="var(--office-shadow)"/>
      </linearGradient>
      <radialGradient id="office-glow" cx="0.3" cy="0.15" r="0.6">
        <stop offset="0" stop-color="#fff6dc" stop-opacity="0.65"/>
        <stop offset="1" stop-color="#fff6dc" stop-opacity="0"/>
      </radialGradient>
      <linearGradient id="residence-tone" x1="0" y1="0" x2="0" y2="1">
        <stop offset="0" stop-color="var(--residence-deep)"/>
        <stop offset="0.3" stop-color="var(--residence-mid)"/>
        <stop offset="0.7" stop-color="var(--residence-light)"/>
        <stop offset="1" stop-color="var(--residence-deep)"/>
      </linearGradient>
      <radialGradient id="residence-glow" cx="0.55" cy="0.12" r="0.55">
        <stop offset="0" stop-color="#9a9ea6" stop-opacity="0.45"/>
        <stop offset="1" stop-color="#9a9ea6" stop-opacity="0"/>
      </radialGradient>
    </defs>
    <g class="office-photo" role="img" aria-label="Bright open-plan office with desks, lounge chairs and leafy plants under a warm golden tint">
      <polygon points="0,0 673,0 536,557 0,557" fill="url(#office-tone)"/>
      <polygon points="0,0 673,0 536,557 0,557" fill="url(#office-glow)"/>
    </g>
    <g class="residence-photo" role="img" aria-label="Dark luxury bedroom with a made bed, slatted wall and bedside lamp">
      <polygon points="673,0 1200,0 1200,557 536,557" fill="url(#residence-tone)"/>
      <polygon points="673,0 1200,0 1200,557 536,557" fill="url(#residence-glow)"/>
    </g>
    <line class="divider" x1="674" y1="-2" x2="537" y2="559" stroke="var(--gold)" stroke-width="6"/>
  </svg>

  <section class="brand-panel brand-panel--office">
    <span class="brand-mark" aria-hidden="true"></span>
    <p class="brand-name">Velmor Spire Nine</p>
    <h1 class="space-title">OFFICE</h1>
    <a class="enter-button enter-button--outline" href="#office">ENTER</a>
  </section>

  <section class="brand-panel brand-panel--residence">
    <span class="brand-mark" aria-hidden="true"></span>
    <p class="brand-name">Velmor Spire Nine</p>
    <h2 class="space-title">RESIDENTIAL</h2>
    <a class="enter-button enter-button--solid" href="#residential">ENTER</a>
  </section>
</main>
</body>
</html>
```